Yard sign design for high end luxury home builder.

Need a design for signage on custom homes that are being built. I already have a logo that I am satisfied with that needs to be incorporated. I need the following incorporated in the design of the sign-
- Lic number 381526
- phone number (805) 555-0148‬
- quennbuilderscrew.com
- Logo/Branding

If possible it may be nice to have the following quote that is on are business cards-

Quote from Gerard of Norvelle-
HE WHO WORKS WITH HIS HANDS IS A LABORER.
HE WHO WORKS WITH HIS HANDS & HIS HEAD IS A CRAFTSMAN.
HE WHO WORKS WITH HIS HANDS & HIS HEAD & HIS HEART IS AN ARTISAN.
-GERARD OF NORVELLE

Target Market(s)

Archetect, Designers, Clients desiring to build a new home or remodel.

Colors
fde9d4
fee4d5
fabb94
fac994
faa54b
f68d4d
f37122
f78f20
f68e4e

Requirements
Must have
• - Lic number 381526
• - phone number (805) 555-0148‬
• - quennbuilderscrew.com
• - Logo/Branding
Nice to have
• Quote from Gerard of Norvelle-
• HE WHO WORKS WITH HIS HANDS IS A LABORER.
• HE WHO WORKS WITH HIS HANDS & HIS HEAD IS A CRAFTSMAN.
• HE WHO WORKS WITH HIS HANDS & HIS HEAD & HIS HEART IS AN ARTISAN.
• -GERARD OF NORVELLE
• OR the below statement-
• Craftsmen that Care
Should not have
• Any additional verbiage not specified above including any type of verbiage about what kind of company we are. For instance- Integrity, reputable... It's just all played out. Im just looking for a bitching design that has the info that compliments my logo/branding.

```html
<!DOCTYPE html>
<html lang="en">
<head>
<meta charset="utf-8">
<title>Quenn Builders Inc. — Yard Sign</title>
<link rel="stylesheet" href="https://fonts.googleapis.com/css2?family=Arimo:wght@400;700&display=swap">
<style>
  :root {
    --ink: #0b0c0c;
    --paper: #ffffff;
    --tan: #a88d6e;
  }
  html, body {
    margin: 0;
    padding: 0;
    width: 1200px;
    height: 1200px;
    overflow: hidden;
    background: var(--paper);
  }
  .yard-sign {
    display: block;
    width: 1200px;
    height: 1200px;
    font-family: "Arimo", Arial, sans-serif;
  }
  .frame-band, .brand-corner, .license-corner { fill: var(--ink); }
  .sign-face { fill: var(--paper); }
  .quote-line { fill: var(--ink); font-weight: 700; }
  .quote-line--small { font-size: 79px; }
  .quote-line--large { font-size: 151px; }
  .brand-name { fill: var(--tan); font-weight: 700; }
  .brand-name--main { font-size: 46px; letter-spacing: 4px; }
  .brand-name--sub { font-size: 14px; letter-spacing: 1.5px; }
  .phone { fill: var(--tan); font-weight: 700; font-size: 95px; }
  .website { fill: var(--ink); font-weight: 400; font-size: 41px; }
  .license-label { fill: var(--paper); font-weight: 700; font-size: 39px; }
  .license-number { fill: var(--tan); font-weight: 700; font-size: 66px; }
</style>
</head>
<body>
<svg class="yard-sign" viewBox="0 0 1200 1200" xmlns="http://www.w3.org/2000/svg">
  <!-- sign board with black frame -->
  <rect class="frame-band" x="25" y="232" width="1151" height="735"/>
  <rect class="sign-face" x="27" y="264" width="1147" height="692"/>

  <!-- brand corner -->
  <polygon class="brand-corner" points="25,262 368,262 276,531 25,531"/>
  <text class="brand-name brand-name--main" x="60" y="470">QUENN</text>
  <text class="brand-name brand-name--sub" x="61" y="494">BUILDERS INC.</text>

  <!-- quote -->
  <text class="quote-line quote-line--small" x="1130" y="416" text-anchor="end">HE WHO WORKS</text>
  <text class="quote-line quote-line--small" x="1130" y="524" text-anchor="end">WITH HIS HANDS</text>
  <text class="quote-line quote-line--large" x="1129" y="674" text-anchor="end">IS A LABORER</text>

  <!-- contact -->
  <text class="phone" x="62" y="848">(805) 555-0148</text>
  <text class="website" x="77" y="924">www.quennbuilderscrew.com</text>

  <!-- license corner -->
  <polygon class="license-corner" points="855,778 1176,778 1176,966 776,966"/>
  <text class="license-label" x="1145" y="852" text-anchor="end">Lic number</text>
  <text class="license-number" x="1137" y="918" text-anchor="end">381526</text>
</svg>
</body>
</html>
```